Therapy Dog Business need a brochure

I need a brochure designed for my Canine Assisted Therapy business in Victoria Australia. I have a logo already and info and photos to upload.
Best as white background and using the colours from the logo please
Updates

Hi Everyone,
I am sorry to have to revise the brief. I have added three new photos I was unable to add due to the size. I have had to wait for my photographer to change the size to add them today. I have been really inspired by all the work you have done so far. Thank you.
Could you please add the following on the brochure. (Under the individual dogs photo)
1. Pepper is the white dog. Please add the following under her picture. Pepper is one of the first Court Dogs in Australia. Working in Victoria, she has worked in the following Courts. The Halbrook Inquest Court, The Brindle Hearing Court in Collingwood, and the Fenwick Court in Melbourne CBD. Her ability to use her intuition for clients is inspiring. Please contact us for potential use in Courts. Pepper has worked at the Marlow Constabulary College, and at TALON at Mar Con. She is a stunning dog!
2. Barnaby is the golden dog. Barnaby is Peppers son, and had her instinct of intuition of who needs his help. Barnaby has an incredible soft approach as does his mother Pepper. He is incredibly safe with young children, and yet has a playful nature for adolescents and adults alike. He is soft and caring, and like his mother will go to those who need him most. Barnaby like his mother has worked at Marlow Constabulary, his time at MC included the Marlow Constabulary Directorate (MCD) Both he and his mother have very impressive CV'S!
3. Tansy the black dog. Tansy is my Therapy and Assistance dog "trainer" she is safe and stable with all the dogs and people I train for Therapy Dog Training and Assistance Dog Training. She has also been with me on my journey as a Counsellor and I have been able to work alongside her and Pepper for Counselling sessions.
She is soft, caring, and also intuitive. I am incredibly grateful for her help, as well as Pepper and Barnaby.
ALSO I am so sorry to add this but could you also add the following: Maybe in dot point?
Court Dog Availability
Therapy Dog Visits - Lawyers - Courts - Child Protection
Police Station / Ambulance Station / Fire Station - Visits
Private Therapy Dog Sessions
website and email confirmation coming soon. Thank you

Target Market(s)

First Responders

Requirements
Must have
• All the photos provided.
Should not have
• Generic photos

```html
<!DOCTYPE html>
<html lang="en">
<head>
<meta charset="utf-8">
<title>Kindred Paws – Canine Assisted Therapy Brochure</title>
<link href="https://fonts.googleapis.com/css2?family=Figtree:wght@400;500;600;700;800;900&display=swap" rel="stylesheet">
<style>
  :root{
    --backdrop:#9b9b9b;
    --rust:#b5512c;
    --rust-mid:#8a3529;
    --maroon:#5a1a28;
    --maroon-deep:#4a1520;
    --panel:#5c1e25;
    --amber:#f6a04a;
    --band:#e2984a;
    --cream:#fff4e8;
    --white:#ffffff;
    --photo-blue:#9fb0dc;
  }
  *{box-sizing:border-box;margin:0;padding:0}
  html,body{width:1200px;height:1200px;overflow:hidden}
  body{background:var(--backdrop);font-family:"Figtree",sans-serif;color:var(--white);position:relative}
  .sheet{position:absolute;left:187px;top:102px;width:785px;height:1016px;overflow:hidden;
    background:linear-gradient(180deg,var(--rust) 0%,var(--rust-mid) 48%,var(--maroon) 80%,var(--maroon) 100%)}
  .intro-panel{position:absolute;left:0;top:0;width:414px;height:224px;
    background:linear-gradient(135deg,#5a1c24 0%,#6b2328 60%,#55191f 100%);
    border-right:2px solid var(--amber);border-bottom:2px solid var(--amber);border-bottom-right-radius:52px}
  .intro-panel .silhouette-area{position:absolute;left:150px;top:20px;width:250px;height:202px;border-radius:40px 40px 50px 0;
    background:radial-gradient(ellipse at 55% 45%,rgba(160,60,40,.35),rgba(60,15,20,0) 70%)}
  .intro-panel .copy{position:absolute;left:37px;top:28px;width:360px}
  h1,h2,h3{font-weight:800;line-height:1.08}
  .intro-panel h1{font-size:24px}
  .intro-panel h1 .accent{color:var(--amber);display:block;font-size:26px}
  .intro-panel p{font-size:11.2px;line-height:15.4px;margin-top:9px;font-weight:400}
  .why{position:absolute;left:41px;top:240px;width:380px}
  .benefits{position:absolute;left:449px;top:34px;width:310px}
  .why h2,.benefits h2{font-size:24px;line-height:31px}
  .point{margin-top:14px}
  .point h3{font-size:17px;font-weight:600;display:flex;align-items:center;gap:6px}
  .point h3::before{content:"";width:10px;height:10px;border-radius:50%;background:var(--white);flex:none}
  .point p{font-size:10px;line-height:13.8px;margin-top:7px;padding-left:5px}
  .why .point{margin-top:16px}
  .availability{margin-top:14px;padding-left:5px}
  .availability h4{font-size:13.6px;font-weight:600;line-height:18.5px}
  .checklist{display:grid;grid-template-columns:122px 116px 80px;margin-top:6px;row-gap:1px;list-style:none}
  .checklist li{font-size:10.4px;line-height:13.6px;display:flex;align-items:center;gap:4px}
  .checklist svg{width:9px;height:9px;flex:none}
  .dogs{position:absolute;left:43px;top:561px;width:700px;display:flex;gap:35px}
  .dog{width:210px}
  .dog-photo{position:relative;height:130px;border:2px solid var(--amber);border-radius:9px;overflow:hidden;
    background:linear-gradient(160deg,#b8c4e6 0%,var(--photo-blue) 55%,#8797c7 100%)}
  .dog-photo .subject{position:absolute;inset:0}
  .dog-photo.pale .subject{background:radial-gradient(ellipse at 45% 55%,#efe2c4 0%,#e5d2a8 32%,rgba(229,210,168,0) 60%)}
  .dog-photo.golden .subject{background:radial-gradient(ellipse at 45% 58%,#f1e2bf 0%,#e2cc9c 32%,rgba(226,204,156,0) 62%),linear-gradient(90deg,#d9633b 0,#d9633b 14%,rgba(0,0,0,0) 26%)}
  .dog-photo.dark .subject{background:radial-gradient(ellipse at 52% 58%,#1d1b1e 0%,#252226 30%,rgba(37,34,38,0) 60%),linear-gradient(180deg,#e58b5b 0,#e58b5b 8%,rgba(0,0,0,0) 12%)}
  .name-tag{position:absolute;right:0;bottom:0;width:103px;height:42px;background:var(--panel);
    border-top-left-radius:14px;display:flex;align-items:center;justify-content:center;
    font-size:19px;font-weight:500;font-style:normal;color:var(--white)}
  .dog p{font-size:9px;line-height:12.3px;text-align:center;margin-top:11px;padding:0 1px}
  .closing-band{position:absolute;left:0;top:871px;width:753px;height:145px;background:var(--band)}
  .closing-band .copy{position:absolute;left:41px;top:20px;width:540px}
  .closing-band h2{font-size:25px;color:var(--maroon-deep);font-weight:900}
  .closing-band p{font-size:11px;line-height:15.3px;margin-top:8px;font-weight:600}
  .contacts{position:absolute;left:41px;top:112px;display:flex;gap:30px;font-size:14px;font-weight:600}
  .contacts span{display:flex;align-items:center;gap:6px}
  .contacts svg{width:14px;height:14px}
  .brand-mark{position:absolute;left:580px;top:827px;width:174px;height:174px;border-radius:50%;
    background:var(--cream);border:5px solid var(--amber);display:flex;flex-direction:column;
    align-items:center;justify-content:center;gap:8px}
  .brand-mark .dot{width:30px;height:30px;border-radius:50%;background:var(--maroon)}
  .brand-mark .name{font-size:18px;font-weight:800;color:var(--maroon);letter-spacing:.5px}
</style>
</head>
<body>
<svg width="0" height="0" style="position:absolute">
  <symbol id="tick" viewBox="0 0 10 10"><circle cx="5" cy="5" r="5" fill="#fff"/><path d="M2.8 5.2l1.5 1.5 3-3.2" fill="none" stroke="#8a3529" stroke-width="1.4" stroke-linecap="round" stroke-linejoin="round"/></symbol>
</svg>

<main class="sheet">
  <section class="intro-panel">
    <div class="silhouette-area" role="img" aria-label="Silhouette illustration of a person in a cap seated with a dog"></div>
    <div class="copy">
      <h1>What is Canine <span class="accent">Assisted Therapy?</span></h1>
      <p>Canine Assisted Therapy (CAT) is a unique form of therapy that integrates trained therapy dogs into the healing process. By working alongside licensed therapists, these compassionate and well-trained dogs help support individuals in overcoming emotional, physical, and psychological challenges. This innovative approach promotes healing, reduces stress, and enhances overall well-being.</p>
    </div>
  </section>

  <section class="why">
    <h2>Why Choose Canine Assisted Therapy?</h2>
    <div class="point">
      <h3>Proven Effectiveness</h3>
      <p>Studies and testimonials highlight the positive effects therapy dogs have on emotional, psychological and physical health.</p>
    </div>
    <div class="point">
      <h3>Non-Invasive and Gentle</h3>
      <p>Therapy dogs provide a natural and non-threatening way to engage with patients, making it accessible for individuals who may feel apprehensive about traditional therapy methods.</p>
    </div>
    <div class="point">
      <h3>Safe and Trustworthy</h3>
      <p>All therapy dogs are carefully trained to work with professionals, ensuring that interactions are safe, beneficial, and appropriate for all individuals.</p>
    </div>
  </section>

  <section class="benefits">
    <h2>Benefits of Canine Assisted Therapy</h2>
    <div class="point">
      <h3>Emotional Support and Comfort</h3>
      <p>Therapy dogs provide immediate emotional support, offering comfort and companionship during therapy sessions. Their calming presence helps reduce feelings of anxiety, stress, and depression, and grief, creating a safe and nurturing environment for healing.</p>
    </div>
    <div class="point">
      <h3>Stress Relief and Relaxation</h3>
      <p>Interacting with dogs has been proven to reduce cortisol (stress hormone) levels and increase serotonin and oxytocin, the “feel-good” hormones. This natural relief from stress makes Canine Assisted Therapy an ideal option for individuals dealing with anxiety, trauma, PTSD, and grief,</p>
    </div>
    <div class="point">
      <h3>Improved Mental Health</h3>
      <p>Therapy dogs encourage social interaction, communication, and emotional expression, helping individuals address mental health challenges such as depression, anxiety, PTSD, and grief. The unconditional love and companionship of a dog can foster trust and openness during therapy sessions.</p>
    </div>
    <div class="availability">
      <h4>Court Dog Availability<br>Private Therapy Dog Sessions</h4>
      <ul class="checklist">
        <li><svg><use href="#tick"/></svg>Therapy Dog Visits</li>
        <li><svg><use href="#tick"/></svg>Child Protection</li>
        <li><svg><use href="#tick"/></svg>Fire Station</li>
        <li><svg><use href="#tick"/></svg>Lawyers</li>
        <li><svg><use href="#tick"/></svg>Police Station</li>
        <li><svg><use href="#tick"/></svg>Visits</li>
        <li><svg><use href="#tick"/></svg>Courts</li>
        <li><svg><use href="#tick"/></svg>Ambulance Station</li>
      </ul>
    </div>
  </section>

  <section class="dogs">
    <article class="dog">
      <div class="dog-photo pale">
        <div class="subject" role="img" aria-label="Photo of Pepper, a white Labrador lying on a blue blanket"></div>
        <div class="name-tag">Pepper</div>
      </div>
      <p>Pepper is one of the first Court Dogs in Australia. Working in Victoria, she has worked in the following Courts. The Halbrook Inquest Court, The Brindle Hearing Court in Collingwood, and the Fenwick Court in Melbourne CBD. Her ability to use her intuition for clients is inspiring. Please contact us for potential use in Courts. Pepper has worked at the Marlow Constabulary College, and at TALON at Mar Con. She is a stunning dog!</p>
    </article>
    <article class="dog">
      <div class="dog-photo golden">
        <div class="subject" role="img" aria-label="Photo of Barnaby, a golden Labrador lying on a blue blanket beside an orange cushion"></div>
        <div class="name-tag">Barnaby</div>
      </div>
      <p>Barnaby is the golden dog. Barnaby is Peppers son, and had her instinct of intuition of who needs his help. Barnaby has an incredible soft approach as does his mother Pepper. He is incredibly safe with young children, and yet has a playful nature for adolescents and adults alike. He is soft and caring, and like his mother will go to those who need him most. Barnaby like his mother has worked at Marlow Constabulary, his time at MC included the Marlow Constabulary Directorate (MCD) Both he and his mother have very impressive CV'S!</p>
    </article>
    <article class="dog">
      <div class="dog-photo dark">
        <div class="subject" role="img" aria-label="Photo of Tansy, a black Labrador lying on a blue blanket with orange cushions"></div>
        <div class="name-tag">Tansy</div>
      </div>
      <p>Tansy the black dog. Tansy is my Therapy and Assistance dog "trainer" she is safe and stable with all the dogs and people I train for Therapy Dog Training and Assistance Dog Training. She has also been with me on my journey as a Counsellor and I have been able to work alongside her and Pepper for Counselling sessions.She is soft, caring, and also intuitive. I am incredibly grateful for her help, as well as Pepper and Barnaby.</p>
    </article>
  </section>

  <footer class="closing-band">
    <div class="copy">
      <h2>Join the Healing Journey Today!</h2>
      <p>Whether you are seeking emotional support or mental health improvement, Canine Assisted Therapy offers a unique and compassionate approach to healing. Connect with us today to learn more about how a therapy dog can help enhance your life and well-being.</p>
    </div>
    <div class="contacts">
      <span><svg viewBox="0 0 24 24"><path fill="#fff" d="M6.6 10.8a15.5 15.5 0 0 0 6.6 6.6l2.2-2.2a1 1 0 0 1 1-.25 11.4 11.4 0 0 0 3.6.57 1 1 0 0 1 1 1V20a1 1 0 0 1-1 1A17 17 0 0 1 3 4a1 1 0 0 1 1-1h3.5a1 1 0 0 1 1 1c0 1.25.2 2.46.57 3.6a1 1 0 0 1-.25 1z"/></svg>0400 217 536</span>
      <span><svg viewBox="0 0 24 24"><rect x="2" y="5" width="20" height="14" fill="none" stroke="#fff" stroke-width="1.6"/><path d="M2 5l10 8 10-8" fill="none" stroke="#fff" stroke-width="1.6"/></svg>hello@kindredpaws.example</span>
      <span><svg viewBox="0 0 24 24"><circle cx="12" cy="12" r="10" fill="none" stroke="#fff" stroke-width="1.6"/><ellipse cx="12" cy="12" rx="4.5" ry="10" fill="none" stroke="#fff" stroke-width="1.4"/><path d="M2 12h20M4 7h16M4 17h16" stroke="#fff" stroke-width="1.2"/></svg>www.kindredpaws.example</span>
    </div>
  </footer>

  <div class="brand-mark">
    <span class="dot"></span>
    <span class="name">Kindred Paws</span>
  </div>
</main>
</body>
</html>
```